Business Card Design Competition

We need a business card design for our Internet Marketing company. We require both front and back designs and the final card must be 89x53mm in size, plus crop marks to 91x55mm. Colours as per logo, plus perhaps black and/or grey (#828282).
Final text must be editable (if you can supply an editable Fireworks PNG, even better)...
FRONT TEXT:
Full Name
Position
Address Line
Suburb, State, Postcode
Phone: 0000 000 000
Mobile: 0000 000 000
Email: xxx@brightlanemedia.com.au
Web: www.brightlanemedia.com.au
Rear of card should be a fresh design plus our slogan text: "Putting You Forward" in large font, then in small text "Kestrel Holdings Pty Ltd (ABN: 42 561 903 774)".
Target Market(s)
Small/Medium Businesses
Industry/Entity Type
Business

```html
<!DOCTYPE html>
<html lang="en">
<head>
<meta charset="utf-8">
<title>Business Card – Front and Back</title>
<link rel="stylesheet" href="https://fonts.googleapis.com/css2?family=Arimo:wght@400;700&display=swap">
<style>
  :root {
    --backdrop: #6fbd33;
    --card: #ffffff;
    --brand-green: #6cb92f;
    --text-grey: #5f5f5f;
    --rule-grey: #828282;
  }
  html, body {
    margin: 0;
    padding: 0;
    width: 1200px;
    height: 899px;
    overflow: hidden;
  }
  body {
    position: relative;
    background: var(--backdrop);
    font-family: "Arimo", Arial, sans-serif;
  }
  .card {
    position: absolute;
    background: var(--card);
  }
  .card--back {
    left: 457px;
    top: 410px;
    width: 590px;
    height: 351px;
  }
  .card--front {
    left: 146px;
    top: 111px;
    width: 587px;
    height: 354px;
    box-shadow: 4px 6px 8px rgba(0, 0, 0, 0.28);
    z-index: 2;
  }
  .front__position {
    position: absolute;
    left: 47px;
    top: 245px;
    margin: 0;
    font-size: 42px;
    font-weight: 700;
    line-height: 1;
    color: var(--brand-green);
  }
  .front__divider {
    position: absolute;
    left: 268px;
    top: 242px;
    width: 1px;
    height: 69px;
    background: var(--rule-grey);
  }
  .front__contact {
    position: absolute;
    left: 293px;
    top: 238px;
    margin: 0;
    font-style: normal;
    font-size: 12.5px;
    line-height: 16px;
    color: var(--text-grey);
  }
  .back__slogan {
    position: absolute;
    left: 0;
    right: 0;
    top: 149px;
    margin: 0;
    text-align: center;
    font-size: 42px;
    font-weight: 700;
    line-height: 1;
    color: var(--brand-green);
  }
  .back__company {
    position: absolute;
    left: 0;
    right: 0;
    top: 195px;
    margin: 0;
    text-align: center;
    font-size: 10.5px;
    font-weight: 700;
    color: var(--brand-green);
  }
</style>
</head>
<body>
  <section class="card card--back" aria-label="Card back">
    <h1 class="back__slogan">Putting You Forward</h1>
    <p class="back__company">Kestrel Holdings Pty Ltd (ABN: 42 561 903 774)</p>
  </section>

  <section class="card card--front" aria-label="Card front">
    <h2 class="front__position">POSITION</h2>
    <div class="front__divider"></div>
    <address class="front__contact">
      123, Sample House, Nr. sample landmark,<br>
      Suburb, Quinsland State. 38001<br>
      Ph. : +6-9876 9876,Mo.&nbsp; +6-987 987 9876<br>
      xxxx@brightlanemedia.com.au<br>
      www.brightlanemedia.com.au
    </address>
  </section>
</body>
</html>
```